Business Card Design For A Cajun Seafood Restaurant

We are opening a cajun seafood restaurant in a week. We mainly serve cajun seafood which is orginally from Louisiana. We want design on both sides of a business card. I have menu on the website. You can go to www.reednkettle.example to check out our menu.

Restaurant name: Reed N' Kettle
Phone: +1 (555) 304-7712
Address: 48206 Ludlow Row, #7, Bexmoor Flats, Ca90000
Email: reednkettle@mailbox.example
Website: www.reednkettle.example

Maybe add social media icons (facebook, instagram) if looks nice on the business card.
facebook.com/reednkettle
instagram.com/reednkettle or @reednkettle

Attached is the logo and other business card samples that I like.

```html
<!DOCTYPE html>
<html lang="en">
<head>
<meta charset="utf-8">
<title>Reed N' Kettle – Business Card</title>
<link href="https://fonts.googleapis.com/css2?family=Roboto:wght@400;500;700&display=swap" rel="stylesheet">
<style>
  :root {
    --page-bg: #e7e7e6;
    --kraft: #b99c74;
    --kraft-dark: #a88a62;
    --sunflower: #e8b80f;
    --sunflower-deep: #d9a707;
    --ink: #1e1a14;
    --crab-orange: #e0662a;
    --corn-yellow: #f2cf3c;
    --card-shadow: 0 3px 6px rgba(0,0,0,0.25);
  }
  * { margin: 0; padding: 0; box-sizing: border-box; }
  html, body {
    width: 1200px; height: 576px; overflow: hidden;
    background: var(--page-bg);
    font-family: "Roboto", Arial, sans-serif;
    color: var(--ink);
  }
  .canvas { position: relative; width: 1200px; height: 576px; }
  .card {
    position: absolute; width: 484px; height: 292px;
    border-radius: 8px; box-shadow: var(--card-shadow); overflow: hidden;
  }
  .card--back { left: 82px; top: 140px; background: var(--kraft); }
  .card--front { left: 602px; top: 138px; background: linear-gradient(135deg, var(--sunflower) 0%, var(--sunflower-deep) 100%); }

  .mascot { position: absolute; border-radius: 40%; }
  .card--back .mascot {
    left: 158px; top: 44px; width: 184px; height: 180px;
    background: radial-gradient(circle at 50% 50%, rgba(40,32,22,0.35) 0%, rgba(40,32,22,0.12) 55%, rgba(40,32,22,0) 72%);
  }
  .card--front .mascot {
    left: 42px; top: 48px; width: 204px; height: 194px;
    background: radial-gradient(circle at 50% 35%, var(--corn-yellow) 0%, var(--crab-orange) 45%, rgba(224,102,42,0) 72%);
  }

  .social-strip {
    position: absolute; left: 0; right: 0; top: 262px;
    display: flex; align-items: center; justify-content: center; gap: 8px;
    font-size: 14px;
  }
  .social-strip .rule { width: 72px; height: 2px; background: var(--ink); border-radius: 2px; }
  .social-strip .rule--left { margin-right: 6px; }
  .social-strip .rule--right { margin-left: 6px; }
  .square-mark { width: 10px; height: 10px; background: var(--ink); border-radius: 2px; display: inline-block; }

  .details { position: absolute; left: 272px; top: 52px; }
  .details .name { font-size: 19px; font-weight: 700; line-height: 1.2; }
  .details .role { font-size: 11px; margin-bottom: 16px; }
  .details .address { font-size: 12.5px; line-height: 18px; margin-bottom: 6px; }
  .contact-list { list-style: none; font-size: 12.5px; }
  .contact-list li { display: flex; align-items: center; height: 18.5px; }
  .contact-list .icon { width: 10px; height: 10px; margin-right: 11px; flex: none; }
</style>
</head>
<body>
<div class="canvas">

  <section class="card card--back">
    <div class="mascot" role="img" aria-label="Line-drawn crab mascot holding an ear of corn"></div>
    <div class="social-strip">
      <span class="rule rule--left"></span>
      <span class="square-mark"></span><span>/Reednkettle</span>
      <span class="square-mark"></span><span>@reednkettle</span>
      <span class="rule rule--right"></span>
    </div>
  </section>

  <section class="card card--front">
    <div class="mascot" role="img" aria-label="Colour crab mascot holding an ear of corn"></div>
    <div class="details">
      <p class="name">Dana Whitlow</p>
      <p class="role">Director</p>
      <p class="address">48206 Ludlow Row, #7,<br>Bexmoor Flats, Ca90000</p>
      <ul class="contact-list">
        <li>
          <svg class="icon" viewBox="0 0 10 10"><path d="M1 3.5C1 2 2 1.5 5 1.5S9 2 9 3.5H7V2.8H3v.7Z M2.5 4.5h5L9 9H1Z" fill="#1e1a14"/></svg>
          +1 (555) 304-7712
        </li>
        <li>
          <svg class="icon" viewBox="0 0 10 10"><rect x="0.5" y="2" width="9" height="6.5" fill="#1e1a14"/><path d="M0.5 2 5 5.8 9.5 2" stroke="#e8b80f" stroke-width="1" fill="none"/></svg>
          reednkettle@mailbox.example
        </li>
        <li>
          <svg class="icon" viewBox="0 0 10 10"><circle cx="5" cy="5" r="4.3" stroke="#1e1a14" stroke-width="1.1" fill="none"/><ellipse cx="5" cy="5" rx="1.8" ry="4.3" stroke="#1e1a14" stroke-width="0.9" fill="none"/><path d="M0.7 5h8.6" stroke="#1e1a14" stroke-width="0.9"/></svg>
          www.reednkettle.example
        </li>
        <li><span class="square-mark icon"></span>facebook.com/reednkettle</li>
        <li><span class="square-mark icon"></span>instagram.com/reednkettle</li>
      </ul>
    </div>
  </section>

</div>
</body>
</html>
```